PostCard Design Project

I am making a mailing postcard
I am having the mailing printed using 4 color foil on certain parts.
I am looking for a design that maximizes the foil process where certain parts are done in foil to grab the customers attention (example: if there is a car on the postcard the headlights would be done in foil) .
I am targeting some industries, (auto, real estate, medical, beauty) I would like the post card to have examples of postcard ideas for 2 or 3 of these industries.
specs:
the postcard should be atleast 6.5x9 up to 8.5x11, I don't want to restrict the space for the creative as I don't want everything to look like a huge mess. both sides will be used.
the piece is a direct mail piece so it has to meet requirements of https://www.mailvantor.com/business/pdf/quick-reference-guide.pdf
text will be
"business with no limits, meet mailing with no addresses, gain new customers through "Open Porch Route Drop" reach new customers at their home without needing their address. "
I also want some current print specials I am running included.
-double your order FREE (order 500 business cards and get 1000)
-250 100lb gloss stock brochures 99.00
-business packages (cards, envelopes and letterhead) 299
-1000 flyers 140.40
-5000 postcards 179.99
A list of services
banners
booklets
brochures
business cards
calendars
catalogs
CD/DVD packages
envelopes
event tickets
flyers
hangtags
postcards
posters
presentation folders
rack cards
labels
table tents
window cling and decal
"order 24/7 orders@inkwillow.com" must be included
my logo is InkWillow will be supplied later
ive received some great designs. however Im looking for something a little more modern like some zorvel would put out. if the amount of words is too much please feel free to edit. also an idea i had for the list of services i offer is to have it transparent yet readable as the background of the postcard some small some big but covering the entire backgroud. you can then design on top of that with other thing. just an early morning thought
Reason: I have uploaded a sketch of my idea, please take time to look at it for an accurate depiction of what im looking for. feel free to add elements that make it pop off the page
Reason: We are getting close i will be providing feed back today

```html
<!DOCTYPE html>
<html lang="en">
<head>
<meta charset="utf-8">
<title>InkWillow Postcard</title>
<link rel="stylesheet" href="https://fonts.googleapis.com/css2?family=Cabin:wght@400;500;600;700&family=Marcellus&display=swap">
<style>
  :root {
    --ink: #2b2828;
    --ink-deep: #1d1b1b;
    --paper: #f4f4f4;
    --white: #ffffff;
    --red: #d51d27;
    --red-frame: #c4161c;
    --orange: #f9b14b;
    --gold: #f6a623;
    --gold-light: #fbc35a;
    --box-text: #2a2220;
  }
  * { box-sizing: border-box; margin: 0; padding: 0; }
  html, body { width: 963px; height: 1200px; overflow: hidden; background: var(--paper); }
  .postcard {
    position: relative;
    width: 963px;
    height: 1200px;
    overflow: hidden;
    font-family: "Cabin", "Trebuchet MS", sans-serif;
    color: var(--white);
    background:
      radial-gradient(ellipse 260px 520px at 100% 20%, rgba(255,255,255,0.35), rgba(255,255,255,0) 70%),
      linear-gradient(to bottom, var(--ink) 0%, var(--ink) 74%, #6f6c6c 86%, #d9d9d9 96%, var(--paper) 100%);
    border-bottom: 3px solid var(--ink-deep);
  }
  .headline {
    position: absolute; left: 27px; top: 18px;
    font-size: 66px; font-weight: 500; letter-spacing: 0.5px; white-space: nowrap;
  }
  .shine {
    position: absolute; left: 22px; top: 118px;
    font-family: "Marcellus", Georgia, serif;
    font-size: 116px; letter-spacing: 3px; color: var(--red);
    -webkit-text-stroke: 1.5px #f3d6d8;
  }
  .logo-slot {
    position: absolute; left: 680px; top: 110px;
    font-size: 31px; font-weight: 700; letter-spacing: 0.5px;
  }
  .order-hours, .order-email {
    position: absolute; left: 24px;
    font-weight: 600; color: var(--gold);
    background: linear-gradient(to bottom, var(--gold-light), var(--gold));
    -webkit-background-clip: text; background-clip: text;
    -webkit-text-fill-color: transparent;
  }
  .order-hours { top: 266px; font-size: 45px; }
  .order-email { top: 336px; font-size: 46px; }

  .photo {
    position: absolute;
    border: 4px solid var(--red-frame);
    border-radius: 12px;
    overflow: hidden;
  }
  .photo-dental {
    left: 663px; top: 186px; width: 223px; height: 218px;
    background: linear-gradient(160deg, #8d8a86 0%, #c9b2a0 45%, #e7d2c2 70%, #6f6a66 100%);
  }
  .photo-dental .industry-tag {
    position: absolute; left: 0; right: 0; bottom: 2px;
    text-align: center; font-size: 36px; font-weight: 700; letter-spacing: 3px;
    color: var(--red); -webkit-text-stroke: 1px #fbe4e4;
  }
  .photo-beauty {
    left: 327px; top: 421px; width: 277px; height: 273px;
    background: linear-gradient(135deg, #f2ece6 0%, #e8cdb8 40%, #d9b199 65%, #f5efea 100%);
  }
  .photo-auto {
    left: 631px; top: 421px; width: 299px; height: 285px;
    background: linear-gradient(150deg, #e33a35 0%, #c41a1c 40%, #3a2a2a 70%, #b9181b 100%);
  }

  .services-title {
    position: absolute; left: 44px; top: 578px;
    font-size: 46px; font-weight: 500; letter-spacing: 1px;
  }
  .services-title span:nth-child(1) { color: #f7941d; }
  .services-title span:nth-child(2) { color: #f2e51c; }
  .services-title span:nth-child(3) { color: #8cc63f; }
  .services-title span:nth-child(4) { color: #29abe2; }
  .services-title span:nth-child(5) { color: #2e3192; }
  .services-title span:nth-child(6) { color: #ed1c24; }
  .services-title span:nth-child(7) { color: #ec008c; }
  .services-title span:nth-child(8) { color: #92278f; }

  .services-list {
    position: absolute; left: 48px; top: 638px;
    list-style: none; font-size: 22px; line-height: 31.2px;
  }
  .services-list li { display: flex; align-items: center; }
  .services-list li::before {
    content: ""; width: 7px; height: 7px; border-radius: 50%;
    background: var(--dot, #8cc63f); margin-right: 10px;
  }

  .mail-pitch {
    position: absolute; left: 288px; top: 714px; width: 345px;
    font-size: 12.5px; line-height: 16px;
  }
  .specials-title {
    position: absolute; left: 486px; top: 782px;
    font-size: 29px; line-height: 27px; font-weight: 600; color: var(--orange);
  }
  .special {
    position: absolute;
    display: flex; align-items: center; justify-content: center;
    text-align: center; border-radius: 14px;
    font-size: 17px; font-weight: 700; line-height: 21px;
    padding: 8px;
  }
  .special-orange { background: var(--orange); color: var(--box-text); }
  .special-red { background: var(--red); color: var(--white); }
  .special-double   { left: 288px; top: 822px;  width: 186px; height: 140px; }
  .special-brochure { left: 482px; top: 873px;  width: 166px; height: 130px; }
  .special-package  { left: 288px; top: 972px;  width: 193px; height: 140px; }
  .special-postcard { left: 491px; top: 1013px; width: 138px; height: 107px; }
  .special-flyers   { left: 385px; top: 1098px; width: 124px; height: 85px; }

  .postal-panel {
    position: absolute; left: 698px; top: 728px; width: 232px; height: 438px;
    background: var(--ink-deep);
    border: 1.5px solid #d8d8d8; border-radius: 14px;
  }
  .stamp-box {
    position: absolute; left: 106px; top: 17px; width: 106px; height: 80px;
    background: var(--white); border: 3px solid var(--red-frame); border-radius: 12px;
  }
  .postal-label {
    position: absolute; left: 18px; top: 122px;
    font-size: 42px; font-weight: 600; line-height: 52px;
  }
</style>
</head>
<body>
<main class="postcard">
  <h1 class="headline">Let Us Help Your Business</h1>
  <p class="shine">SHINE !</p>
  <p class="logo-slot">LOGO HERE</p>
  <p class="order-hours">24 hr/ 7day</p>
  <p class="order-email">Order@inkwillow.com</p>

  <div class="photo photo-dental" role="img" aria-label="Photo of a smiling dental receptionist wearing a headset">
    <span class="industry-tag">Dental</span>
  </div>
  <div class="photo photo-beauty" role="img" aria-label="Beauty portrait of a woman with styled hair"></div>
  <div class="photo photo-auto" role="img" aria-label="Close-up of a red sports car headlight and grille"></div>

  <h2 class="services-title"><span>S</span><span>e</span><span>r</span><span>v</span><span>i</span><span>c</span><span>e</span><span>s</span></h2>
  <ul class="services-list">
    <li style="--dot:#8cc63f">banners</li>
    <li style="--dot:#29abe2">booklets</li>
    <li style="--dot:#2e3192">brochures</li>
    <li style="--dot:#ec008c">business cards</li>
    <li style="--dot:#f2e51c">calendars</li>
    <li style="--dot:#f7941d">catalogs</li>
    <li style="--dot:#ed1c24">CD/DVD packages</li>
    <li style="--dot:#f7941d">envelopes</li>
    <li style="--dot:#f2e51c">event tickets</li>
    <li style="--dot:#39b54a">flyers</li>
    <li style="--dot:#8cc63f">hangtags</li>
    <li style="--dot:#00a99d">postcards</li>
    <li style="--dot:#29abe2">posters</li>
    <li style="--dot:#2e3192">presentation folders</li>
    <li style="--dot:#662d91">rackcards</li>
    <li style="--dot:#cccccc">labels</li>
  </ul>

  <p class="mail-pitch">Business with no limits, meet mailing with no addresses, gain new customers through "Open Porch Route Drop" reach new customers at their home without needing their address.</p>

  <p class="specials-title">current<br>specials<br>print</p>
  <div class="special special-orange special-double">Double your order FREE (order 500 business cards and get 1000)</div>
  <div class="special special-orange special-brochure">250 100lb gloss stock brochures 99.00</div>
  <div class="special special-red special-package">Business packages (cards, envelopes and letterhead) 299</div>
  <div class="special special-orange special-postcard">5000 postcards 179.99</div>
  <div class="special special-red special-flyers">1000 flyers 140.40</div>

  <section class="postal-panel">
    <div class="stamp-box"></div>
    <p class="postal-label">Postal<br>Customer</p>
  </section>
</main>
</body>
</html>
```